Valdo Capital

We need a corporate style website design for a new company based in Shenzhen's Qianhai Special Economic Development Zone, China. We provide a range of financial services to large international investment companies. Typically these companies invest over 5 million RMB. The company is part of a group that consists of NorthKilns, ValdoTrusts and ValdoEquity. Our location and gateway into Qianhai Special Economic Zone is our core advantage. We would like to see designs that Do Not use purple and orange. The website design should be similar to other websites in this family but different enough to give it a unique style (See attached website links for reference). The final design should communicate financial safety and growth. This website will act partly as a business chamber with connections to the government so we would like it to be diplomatic in style.

www.northkilns.example
www.valdotrusts.example

*Nevegation Bar
Should including Homepage, Financial Product, Team, News.
Could refer to www.valdotrusts.example

*Contact Details

Miss Lan
Address:E 728, North Block, KMO Centre, East Sector, Shenzhen Bright Science Campus
Telephone: +86 0755 63920417
Cellphone: +86 13957280316

* Social Media
Should be grouped like:
1. Weibo QRcode+ Weibo
2. Facebook, Twitter, Linkedin.

Industry/Entity Type

Investment

```html
<!DOCTYPE html>
<html lang="en">
<head>
<meta charset="utf-8">
<title>Valdo Capital</title>
<link href="https://fonts.googleapis.com/css2?family=Cinzel:wght@400;700&family=Arimo:wght@400;700&family=Caveat:wght@600&display=swap" rel="stylesheet">
<style>
:root{
  --blue:#2a87b8;
  --blue-dark:#1d6f9c;
  --navy:#0b1f6b;
  --ink:#222;
  --grey:#666;
  --light:#f1f1f1;
  --line:#dcdcdc;
  --footer:#1e1e1e;
  --ticker:#141414;
  --white:#fff;
}
*{box-sizing:border-box;margin:0;padding:0}
html,body{width:770px;height:1200px;overflow:hidden;background:var(--white)}
body{font-family:"Arimo",Arial,sans-serif;color:var(--ink);font-size:7px}
.page{position:relative;width:770px;height:1200px;overflow:hidden;background:linear-gradient(#fff 0,#fff 880px,#f4f4f4 1043px)}
.abs{position:absolute}

/* header */
.header{left:0;top:0;width:770px;height:52px;background:var(--white);box-shadow:0 1px 3px rgba(0,0,0,.15);z-index:3}
.brand{left:98px;top:9px;display:flex;align-items:center;gap:8px}
.brand-mark{width:34px;height:34px;background:var(--navy);border-radius:50%}
.brand-name{font-family:"Arimo",Arial,sans-serif;font-weight:400;font-size:18px;color:#111;line-height:1}
.lang{left:613px;top:5px;width:60px;height:13px;background:#e6e6e6;border:1px solid #ccc;font-size:6px;color:#555;padding:2px 5px}
.lang-btn{left:661px;top:5px;width:12px;height:13px;background:var(--blue)}
.nav{left:380px;top:25px;display:flex;align-items:center;font-family:"Cinzel",serif;font-size:9px}
.nav a{color:#111;text-decoration:none;padding:4px 9px}
.nav a.active{background:var(--blue);color:var(--white);border-radius:2px}

/* hero */
.hero{left:0;top:52px;width:770px;height:354px;background:radial-gradient(circle at 55% 45%,#1b3fc4 0,#0a1f86 40%,#040c38 75%,#02061c 100%)}
.hero-title{left:0;top:120px;width:770px;text-align:center;font-family:"Cinzel",serif;font-weight:400;font-size:30px;line-height:36px;color:var(--white);letter-spacing:1px}
.portraits{left:281px;top:172px;display:flex;gap:13px}
.portrait{width:60px;height:60px;border-radius:50%;border:3px solid var(--white);background:linear-gradient(#d8dde4,#9aa6b6)}
.hero-text{left:200px;top:241px;width:370px;text-align:center;color:var(--white);font-size:13px;line-height:15px}
.hero-btn{left:351px;top:282px;width:66px;height:23px;background:var(--blue);color:var(--white);font-size:11px;font-weight:700;text-align:center;line-height:23px;border-radius:2px;box-shadow:0 1px 3px rgba(0,0,0,.5)}
.know{left:427px;top:300px;font-family:"Caveat",cursive;color:var(--white);font-size:13px}
.dots{left:361px;top:356px;display:flex;gap:4px}
.dot{width:9px;height:9px;border-radius:50%;background:#ddd}
.dot.on{background:var(--blue)}

/* welcome */
.ornament{top:406px;width:70px;height:60px;background:linear-gradient(#f4ecee,#fff)}
.welcome{left:97px;top:383px;width:575px;height:182px;background:linear-gradient(#fff,#f4f4f4);border-top:3px solid var(--blue);box-shadow:0 1px 4px rgba(0,0,0,.15);text-align:center;padding:25px 30px}
.welcome h2{font-weight:400;font-size:17px;color:#333;line-height:1}
.welcome h1{font-weight:400;font-size:26px;color:var(--blue);line-height:1.2;margin-bottom:8px}
.welcome p{font-size:5.6px;line-height:8px;color:#333;margin-bottom:8px}

/* feature cards */
.features{left:123px;top:566px;width:523px;height:181px;border:1px solid var(--line);background:var(--white);box-shadow:0 1px 3px rgba(0,0,0,.08)}
.card{top:15px;width:113px}
.card-img{width:113px;height:78px}
.card h3{font-size:10px;font-weight:400;color:var(--blue);margin:5px 0 4px}
.card p{font-size:5.5px;line-height:7.5px;color:#555}
.card .more{display:inline-block;margin-top:5px;font-size:5.5px;padding:2px 5px;background:#eee;color:var(--blue)}
.card .more.dark{background:#222;color:var(--white)}
.slide-arrow{top:643px;width:16px;height:26px;background:var(--blue)}

/* columns */
.col-title{font-size:11px;font-weight:400;color:#111}
.divider{top:784px;width:1px;height:175px;background:var(--line)}
.quote{width:162px;background:var(--blue);color:var(--white);padding:6px 12px;font-size:5.6px;line-height:7.5px;font-weight:700}
.writer{font-size:6px;color:#111;text-align:right;width:162px}
.news-date{font-size:6.5px;color:var(--navy);font-weight:700}
.news-head{font-size:6.5px;color:var(--navy);font-weight:700;margin:3px 0}
.news-body{font-size:5.6px;line-height:7.5px;color:#555;width:140px}
.news-more{font-size:6px;color:var(--navy);text-align:right;width:140px}
.tweet{width:125px;font-size:5.6px;line-height:7.5px;color:#444;padding-left:15px;position:absolute}
.tweet::before{content:"";position:absolute;left:0;top:2px;width:9px;height:9px;border-radius:50%;background:#333}
.tweet .link{color:var(--blue)}
.tweet .ago{font-style:italic;color:#333}
.skyline{left:0;top:920px;width:770px;height:123px;background:linear-gradient(rgba(230,230,230,0),#e2e2e2 70%,#ececec)}

/* ticker */
.ticker{left:0;top:1043px;width:770px;height:42px;background:var(--ticker)}
.ticker-label{left:107px;top:1057px;color:var(--white);font-size:10.5px}
.ticker-date{left:247px;top:1050px;width:66px;height:26px;background:#2b2b2b;color:#aaa;font-size:6.5px;line-height:26px;text-align:center}
.ticker-text{left:313px;top:1050px;width:324px;height:26px;background:#202020;color:var(--blue);font-size:6.5px;line-height:26px;padding-left:10px}
.ticker-ctrl{left:637px;top:1050px;width:26px;height:26px;background:#000}

/* footer */
.footer{left:0;top:1085px;width:770px;height:115px;background:var(--footer)}
.contact{top:1111px;display:flex;align-items:center;gap:8px;color:var(--white);font-size:11.5px}
.contact .ic{width:22px;height:22px;border-radius:50%;background:var(--blue)}
.contact.phone{font-size:14px}
.foot-rule{left:107px;top:1157px;width:556px;height:1px;background:#333}
.foot-nav{left:107px;top:1171px;display:flex;gap:8px;font-size:6px;font-weight:700;color:var(--white)}
.foot-nav .active{color:var(--blue)}
.copy{left:107px;top:1183px;font-size:4.8px;color:#888}
.stay{left:542px;top:1170px;font-family:"Caveat",cursive;color:var(--white);font-size:12px}
.social{left:604px;top:1171px;display:flex;gap:4px}
.social span{width:17px;height:17px;border-radius:50%;background:var(--blue)}
.social span:first-child{background:var(--white)}
</style>
</head>
<body>
<div class="page">

  <header class="header abs">
    <div class="brand abs">
      <div class="brand-mark"></div>
      <div class="brand-name">Valdo Capital</div>
    </div>
    <div class="lang abs">English (UK)</div>
    <div class="lang-btn abs">
      <svg width="12" height="13" viewBox="0 0 12 13"><path d="M3 5h6l-3 4z" fill="#fff"/></svg>
    </div>
    <nav class="nav abs">
      <a class="active">Home</a>
      <a>Financial Product</a>
      <a>Team</a>
      <a>News</a>
      <a>Contact Us</a>
    </nav>
  </header>

  <section class="hero abs" role="img" aria-label="Dark blue circuit board backdrop with currency symbols and binary digits"></section>
  <svg class="abs" style="left:56px;top:202px" width="20" height="40" viewBox="0 0 20 40"><path d="M16 3 4 20l12 17" stroke="#fff" stroke-width="2" fill="none"/></svg>
  <svg class="abs" style="left:694px;top:202px" width="20" height="40" viewBox="0 0 20 40"><path d="M4 3l12 17L4 37" stroke="#fff" stroke-width="2" fill="none"/></svg>
  <h1 class="hero-title abs">LOREM IPSUM DOLOR SIT AMET</h1>
  <div class="portraits abs">
    <div class="portrait" role="img" aria-label="Portrait of a team member"></div>
    <div class="portrait" role="img" aria-label="Portrait of a team member"></div>
    <div class="portrait" role="img" aria-label="Portrait of a team member"></div>
  </div>
  <p class="hero-text abs">Lorem ipsum dolor sit amet, consectetur adipiscing elit. Nulla lobortis consequat mauris, eget eleifend nunc</p>
  <div class="hero-btn abs">Click Here</div>
  <svg class="abs" style="left:400px;top:306px" width="30" height="18" viewBox="0 0 30 18"><path d="M28 10C18 16 8 14 5 4" stroke="#fff" stroke-width="1.2" fill="none"/><path d="M2 7l3-5 3 5" stroke="#fff" stroke-width="1.2" fill="none"/></svg>
  <div class="know abs">Know More</div>
  <div class="dots abs"><span class="dot on"></span><span class="dot"></span><span class="dot"></span><span class="dot"></span></div>

  <div class="ornament abs" style="left:0" role="img" aria-label="Soft pink ornamental corner"></div>
  <div class="ornament abs" style="left:700px" role="img" aria-label="Soft pink ornamental corner"></div>

  <section class="welcome abs">
    <h2>Welcome to</h2>
    <h1>Valdo Capital</h1>
    <p>Lorem ipsum dolor sit amet, consectetur adipiscing elit. Nulla lobortis consequat mauris, eget eleifend nunc viverra viverra. Ut ac risus odio. Aliquam pretium purus sed nulla feugiat blandit. Cras vel libero ut lacus eleifend tempor. Ut ac risus odio. Aliquam pretium purus sed</p>
    <p>Phasellus eleifend, magna non tincidunt accumsan, justo arcu cursus ipsum, non porttitor sapien quam vel magna. Maecenas elit nisl, molestie nec dapibus nec, aliquet a erat. Donec scelerisque lacus a libero suscipit auctor volutpat enim euismod. Mauris porta, lacus ut ullamcorper sodales, mauris tortor feugiat purus, nec aliquam neque purus ac metus. Nunc eleifend leo quis nisl hendrerit ultrices. Suspendisse quis feugiat elit. Fusce vitae dolor ac est tincidunt feugiat. Phasellus volutpat dui in sapien malesuada tempus placerat justo ultricies. Duis mollis ornare risus, ut consectetur mi tincidunt sit amet. Maecenas quis nibh ac. Ut ac risus odio. Aliquam pretium purus sed orci tempus scelerisque ac et massa. Ut ac risus odio. Aliquam pretium purus sed</p>
  </section>

  <section class="features abs">
    <article class="card abs" style="left:15px">
      <div class="card-img" role="img" aria-label="Businesswoman presenting glowing finance graphics" style="background:linear-gradient(135deg,#5a5a5a,#1e1e1e)"></div>
      <h3>Lorem ipsum dolor</h3>
      <p>Sit amet, consectetur adipiscing elit. Nulla lobortis consequat mauris, eget eleifend nunc viverra viverra. Ut ac risus odio. Aliquam pretium purus sed nulla.</p>
      <span class="more">Read more</span>
    </article>
    <article class="card abs" style="left:142px">
      <div class="card-img" role="img" aria-label="City skyline of modern towers" style="background:linear-gradient(#dfe9ec,#8fa7ad)"></div>
      <h3>Lorem ipsum dolor</h3>
      <p>Sit amet, consectetur adipiscing elit. Nulla lobortis consequat mauris, eget eleifend nunc viverra viverra. Ut ac risus odio. Aliquam pretium purus sed nulla.</p>
      <span class="more">Read more</span>
    </article>
    <article class="card abs" style="left:268px">
      <div class="card-img" role="img" aria-label="Couple reviewing documents at a table" style="background:linear-gradient(#f3ede6,#b9a393)"></div>
      <h3>Lorem ipsum dolor</h3>
      <p>Sit amet, consectetur adipiscing elit. Nulla lobortis consequat mauris, eget eleifend nunc viverra viverra. Ut ac risus odio. Aliquam pretium purus sed nulla.</p>
      <span class="more">Read more</span>
    </article>
    <article class="card abs" style="left:395px">
      <div class="card-img" role="img" aria-label="Glasses resting on a newspaper" style="background:linear-gradient(#f5efe6,#c9b9a2)"></div>
      <h3>Lorem ipsum dolor</h3>
      <p>Sit amet, consectetur adipiscing elit. Nulla lobortis consequat mauris, eget eleifend nunc viverra viverra. Ut ac risus odio. Aliquam pretium purus sed nulla.</p>
      <span class="more dark">Read more</span>
    </article>
  </section>
  <div class="slide-arrow abs" style="left:110px;border-radius:13px 0 0 13px">
    <svg width="16" height="26" viewBox="0 0 16 26"><path d="M10 8l-5 5 5 5z" fill="#fff"/></svg>
  </div>
  <div class="slide-arrow abs" style="left:644px;border-radius:0 13px 13px 0">
    <svg width="16" height="26" viewBox="0 0 16 26"><path d="M6 8l5 5-5 5z" fill="#fff"/></svg>
  </div>

  <div class="skyline abs" role="img" aria-label="Faint grey city skyline"></div>

  <section class="testimonials abs" style="left:122px;top:788px">
    <h4 class="col-title">Clients Testimonials</h4>
    <div class="quote" style="margin-top:6px">21-03-2014<br>"Lorem ipsum dolor sit amet, consectetur adipiscing elit. Nulla lobortis consequat mauris, eget eleifend nunc viverra consequat mauris."</div>
    <svg width="162" height="7" viewBox="0 0 162 7" style="display:block"><path d="M140 0h12v7z" fill="#2a87b8"/></svg>
    <div class="writer">Writer Name</div>
    <div class="quote" style="margin-top:10px">21-03-2014<br>"Lorem ipsum dolor sit amet, consectetur adipiscing elit. Nulla lobortis consequat mauris, eget eleifend nunc viverra consequat mauris."</div>
    <svg width="162" height="7" viewBox="0 0 162 7" style="display:block"><path d="M140 0h12v7z" fill="#2a87b8"/></svg>
    <div class="writer">Writer Name</div>
  </section>

  <div class="divider abs" style="left:311px"></div>

  <section class="news abs" style="left:334px;top:788px">
    <h4 class="col-title">Latest News</h4>
    <div style="margin-top:9px">
      <div class="news-date">15/10/2014:</div>
      <div class="news-head">Duis nec augue eget lorem vestibulum</div>
      <p class="news-body">Lorem ipsum dolor sit amet, consectetur adipiscing elit. Nulla lobortis consequat mauris, eget eleifend nunc viverra consequat mauris...</p>
      <div class="news-more">more</div>
    </div>
    <div style="margin-top:8px;border-top:1px dotted #bbb;padding-top:5px;width:140px">
      <div class="news-date">18/10/2014:</div>
      <div class="news-head">Duis nec augue eget lorem vestibulum</div>
      <p class="news-body">Lorem ipsum dolor sit amet, consectetur adipiscing elit. Nulla lobortis consequat mauris, eget eleifend nunc viverra consequat mauris...</p>
      <div class="news-more">more</div>
    </div>
    <div style="margin-top:8px;font-size:6px;color:#111">All the news</div>
  </section>

  <div class="divider abs" style="left:497px"></div>

  <section class="tweets abs" style="left:515px;top:788px;width:140px;height:160px">
    <h4 class="col-title">Latest Tweets</h4>
    <div class="tweet" style="top:19px">Lorem ipsum dolor sit amet, consectetu adipiscing elit, sed diam nonummy nibh<br><span class="link">http://valdocapital.example/</span><br><span class="ago">24 minutes ago</span></div>
    <div class="tweet" style="top:64px">Lorem ipsum dolor sit amet, consectetu adipiscing elit, sed diam nonummy nibh<br><span class="link">http://valdocapital.example/</span><br><span class="ago">28 minutes ago</span></div>
    <div class="tweet" style="top:110px">Lorem ipsum dolor sit amet, consecte adipiscing elit, sed diam nonummy<br><span class="link">http://valdocapital.example/</span><br><span class="ago">29 minutes ago</span></div>
  </section>

  <section class="ticker abs"></section>
  <div class="ticker-label abs">Valdo Capital in the news</div>
  <div class="ticker-date abs">March 05, 2014</div>
  <div class="ticker-text abs">Donec a lectus non purus ultricies eleifend. Duis nec augue eget lorem vestibulum suscipit.</div>
  <div class="ticker-ctrl abs">
    <svg width="26" height="26" viewBox="0 0 26 26"><path d="M12 9l-5 4 5 4z" fill="#2a87b8"/><path d="M15 9l5 4-5 4z" fill="#fff"/></svg>
  </div>

  <footer class="footer abs"></footer>
  <div class="contact phone abs" style="left:107px">
    <span class="ic"><svg width="22" height="22" viewBox="0 0 22 22"><path d="M8 6l2 3-1 1.5c.8 1.6 1.9 2.7 3.5 3.5L14 13l3 2-1 2c-4.5-.3-8.7-4.5-9-9z" fill="#fff"/></svg></span>
    0000 0000 000
  </div>
  <div class="contact abs" style="left:285px">
    <span class="ic"><svg width="22" height="22" viewBox="0 0 22 22"><rect x="6" y="7.5" width="10" height="7" fill="#fff"/><path d="M6 7.5l5 4 5-4" stroke="#2a87b8" fill="none"/></svg></span>
    support@valdocapital.example
  </div>
  <div class="contact abs" style="left:498px">
    <span class="ic"><svg width="22" height="22" viewBox="0 0 22 22"><circle cx="11" cy="11" r="5" fill="none" stroke="#fff" stroke-width="1.5"/><circle cx="11" cy="11" r="1.5" fill="#fff"/></svg></span>
    support@valdocapital.example
  </div>
  <div class="foot-rule abs"></div>
  <nav class="foot-nav abs">
    <span class="active">Home</span><span>Financial Product</span><span>Team</span><span>News</span><span>Contact Us</span>
  </nav>
  <div class="copy abs">COPYRIGHT © 2014 Valdo Capital Limited. TERMS OF USE | PRIVACY POLICY</div>
  <div class="stay abs">Stay with us</div>
  <div class="social abs" aria-label="Social links"><span></span><span></span><span></span></div>

</div>
</body>
</html>
```